Business card for Eyelash extension salon in Beverly Hills,California USA

We need new business card for our salon in Beverly Hills. The salon name is 'Lashvera' . We would like to have...Business name: Lashvera Name of person: will provide later Address 4720 N.Alder Crest Ave Beverly Hills , CA 90210 Phone: will provide later (Text only) Web: www.lashverastudio.example Snapgrid icon, Circlebook icon follow us for seasonal campaign and news @lashverastudiolounge Design should look elegant, high-end, clean, simple, cohesive with my brand. Please refer my brand board. Business name color will be metallic bronzy color. Im thinking grey background or white background. Thanks

Target Market(s)

25-35. Gender neutral. People who are in Entertainment business industry.
This is High-end Eyelash extension salon in Beverly Hills

Industry/Entity Type

Beauty Salon

Contact Information for Business Card

Business name: Lashvera
Name of person: will provide later
Address 4720 N.Alder Crest Ave Beverly Hills , CA 90210
Phone: will provide later (Text only)
Web: www.lashverastudio.example
Snapgrid icon, Circlebook icon
follow us for seasonal campaign and news @lashverastudiolounge

Requirements
Must have
• Beautiful, elegant, clean and simple look but very attractive and modern
Should not have
• We don't like too clutter, too busy designs.

```html
<!DOCTYPE html>
<html lang="en">
<head>
<meta charset="utf-8">
<title>Lashvera Business Card</title>
<link rel="stylesheet" href="https://fonts.googleapis.com/css2?family=Bebas+Neue&family=Work+Sans:wght@300;400&display=swap">
<style>
  :root {
    --backdrop: #262626;
    --card: #1b1b1b;
    --bronze: #8a6650;
    --ink: #ffffff;
  }
  * { margin: 0; padding: 0; box-sizing: border-box; }
  html, body {
    width: 1093px;
    height: 1200px;
    overflow: hidden;
    background: var(--backdrop);
  }
  .canvas {
    position: relative;
    width: 1093px;
    height: 1200px;
  }
  .card {
    position: absolute;
    left: 191px;
    width: 711px;
    height: 411px;
    background: var(--card);
    font-family: "Work Sans", sans-serif;
  }
  .card--front { top: 132px; }
  .card--back { top: 638px; }

  .front-handle {
    position: absolute;
    left: 74px;
    top: 301px;
    font-size: 19px;
    color: var(--bronze);
    letter-spacing: 0.2px;
  }
  .brand {
    position: absolute;
    left: 352px;
    top: 206px;
    width: 290px;
    text-align: center;
    color: var(--bronze);
  }
  .brand__name {
    font-size: 62px;
    font-weight: 300;
    line-height: 1;
    letter-spacing: 1px;
  }
  .brand__place {
    margin-top: 18px;
    font-size: 11px;
    font-weight: 300;
    letter-spacing: 3px;
    text-transform: uppercase;
  }

  .social {
    position: absolute;
    right: 28px;
    top: 30px;
    display: flex;
    align-items: center;
    gap: 10px;
    color: var(--ink);
    font-weight: 300;
    font-size: 19px;
  }
  .social__mark {
    width: 16px;
    height: 16px;
    background: var(--bronze);
    border-radius: 3px;
  }
  .person {
    position: absolute;
    left: 46px;
    top: 183px;
    font-family: "Bebas Neue", sans-serif;
    font-size: 48px;
    line-height: 1;
    color: var(--ink);
    letter-spacing: 1px;
  }
  .divider {
    position: absolute;
    left: 330px;
    top: 172px;
    width: 2px;
    height: 70px;
    background: var(--ink);
  }
  .contact {
    position: absolute;
    left: 361px;
    top: 172px;
    list-style: none;
    color: var(--ink);
    font-size: 19px;
    line-height: 22.5px;
  }
</style>
</head>
<body>
<main class="canvas">
  <section class="card card--front">
    <p class="front-handle">@lashverastudiolounge</p>
    <div class="brand">
      <p class="brand__name">Lashvera</p>
      <p class="brand__place">Beverly Hills</p>
    </div>
  </section>

  <section class="card card--back">
    <p class="social"><span class="social__mark" aria-hidden="true"></span>@marisolden</p>
    <h1 class="person">Marisol Denton</h1>
    <span class="divider" aria-hidden="true"></span>
    <ul class="contact">
      <li>Phone: (310) 555 0148</li>
      <li>Email: marisol@mdenton.example</li>
      <li>Web: www.lashverastudio.example</li>
    </ul>
  </section>
</main>
</body>
</html>
```